AGP letterhead

We need a letterhead design for our new company based in Los Angeles called "Amber Gate Pictures". We develop film and television projects. We work with investors, financiers, film production companies, film distribution and sales companies as well as studios. We would like to incorporate our logo (see attached) but make the letterhead simple and elegant. We need to include: logo, company address, phone number and company website.
Updates

Hello designers, Thanks for your submissions. For our letterhead, we are looking for something more simple and elegant. No heavy bars or lines. Make it feel light and clean. Not a lot of ink on the page. Use the logo and contact info but think "clean", "streamlined" and mostly white paper. Looking forward to seeing more... thanks! Amber Gate Pictures team

Target Market(s)

Studio executives, talent agents and agencies, financiers, investors.

Industry/Entity Type

It Company

Requirements
Must have
• Amber Gate Pictures logo (see attached). Logo may be cropped and altered appropriately for elegant letterhead design.
• Please include:
• COMPANY ADDRESS:
• Tolvane Arts Park
• 2850 Delmore Street
• Crest Hall, 2nd Floor
• Larkmere Cove, CA 90418
• COMPANY WEBSITE:
• www.ambergatepicturesco.example
• COMPANY PHONE NUMBER:
• 555-604-2187

```html
<!DOCTYPE html>
<html lang="en">
<head>
<meta charset="utf-8">
<title>Amber Gate Pictures — Letterhead</title>
<link href="https://fonts.googleapis.com/css2?family=Source+Sans+3:wght@400;600;700&display=swap" rel="stylesheet">
<style>
  :root {
    --backdrop: #e9ecee;
    --paper: #f4f4f5;
    --ink: #3a3f45;
    --accent: #1f8fc4;
    --watermark: #e4e4e6;
  }
  * { margin: 0; padding: 0; box-sizing: border-box; }
  html, body {
    width: 1200px;
    height: 1000px;
    overflow: hidden;
    background: var(--backdrop);
    font-family: "Source Sans 3", "Helvetica Neue", Arial, sans-serif;
  }
  .letterhead {
    position: absolute;
    left: 273px;
    top: 37px;
    width: 654px;
    height: 926px;
    background: var(--paper);
  }
  .brand {
    position: absolute;
    top: 58px;
    left: 0;
    right: 0;
    display: flex;
    justify-content: center;
    align-items: center;
    gap: 12px;
  }
  .brand-square {
    width: 22px;
    height: 22px;
    background: var(--accent);
  }
  .brand-name {
    font-size: 20px;
    font-weight: 600;
    letter-spacing: 0.18em;
    text-transform: uppercase;
    color: var(--ink);
  }
  .watermark {
    position: absolute;
    left: 112px;
    top: 314px;
    width: 430px;
    height: 430px;
  }
  .contact-line {
    position: absolute;
    left: 74px;
    right: 20px;
    top: 876px;
    display: flex;
    gap: 22px;
    font-size: 8px;
    color: var(--ink);
    white-space: nowrap;
  }
  .contact-label {
    font-weight: 700;
    color: var(--accent);
  }
</style>
</head>
<body>
  <main class="letterhead">
    <header class="brand">
      <span class="brand-square" aria-hidden="true"></span>
      <span class="brand-name">Amber Gate Pictures</span>
    </header>

    <svg class="watermark" viewBox="0 0 430 430" aria-hidden="true">
      <circle cx="215" cy="215" r="212" fill="none" stroke="var(--watermark)" stroke-width="4"/>
    </svg>

    <footer class="contact-line">
      <span class="contact-office"><span class="contact-label">Office:</span> Tolvane Arts Park 2850 Delmore Street Crest Hall, 2nd Floor, Larkmere Cove, CA 90418.</span>
      <span class="contact-phone"><span class="contact-label">Tel:</span> 555-604-2187</span>
      <span class="contact-web"><span class="contact-label">Web:</span> www.ambergatepicturesco.example</span>
    </footer>
  </main>
</body>
</html>
```